Veltrane Group Business Card Design

The CEO is looking for a new trendy look for his business card.
You can stay with current branding or come up with something new/creative. It can be 3D, including Medical Office buildings. You can use our logo in a variety of colors. Please include name, title, company name, company website, email address, cell number

Target Market(s)

Real Estate Development and Construction

Industry/Entity Type

Health care real estate

Contact Information for Business Card

Rohesh Kamdar, CEO M-604.781.2249 E-roheshkamdar@veltrane.com Address:4180 Lindqvist Ave, Tampa, FL 33482 www.veltrane.com

Font styles to use
Other font styles liked:
• Be creative

Requirements
Must have
• Creative, trendy look
Nice to have
• Please go to our website to get a feel- www. veltrane.com
Should not have
• small fonts

```html
<!DOCTYPE html>
<html lang="en">
<head>
<meta charset="utf-8">
<title>Veltrane Group Business Card</title>
<link rel="stylesheet" href="https://fonts.googleapis.com/css2?family=Lato:wght@400;700;900&display=swap">
<style>
  :root {
    --stage: #3a3a3a;
    --ink: #000000;
    --paper: #ffffff;
    --card-dark: #0d0d0d;
    --pattern-a: #111111;
    --pattern-b: #2a2a2a;
    --rule: #555555;
  }
  * { box-sizing: border-box; margin: 0; padding: 0; }
  html, body {
    width: 1200px; height: 694px; overflow: hidden;
    background: var(--stage);
    font-family: "Lato", sans-serif;
  }
  .stage {
    position: relative; width: 1200px; height: 694px;
    display: flex; align-items: center; justify-content: center; gap: 60px;
  }
  .card {
    position: relative; width: 520px; height: 300px;
    border-radius: 22px; overflow: hidden;
  }
  /* Back side */
  .card-back { background: var(--card-dark); }
  .card-back .pattern-field {
    position: absolute; inset: 0;
    background: linear-gradient(135deg, var(--pattern-a) 0%, var(--pattern-b) 55%, var(--pattern-a) 100%);
  }
  .card-back .back-name {
    position: absolute; left: 0; right: 0; top: 50%;
    transform: translateY(-50%);
    text-align: center;
    color: var(--paper); font-weight: 900; font-size: 28px; letter-spacing: -0.5px;
  }
  /* Front side */
  .card-front { background: var(--paper); color: var(--ink); }
  .company-name {
    position: absolute; right: 34px; top: 30px;
    font-weight: 900; font-size: 46px; letter-spacing: -1.5px; line-height: 1;
  }
  .person {
    position: absolute; left: 34px; top: 138px; width: 190px; text-align: right;
  }
  .person-name { font-weight: 700; font-size: 24px; line-height: 1.1; }
  .person-title { font-weight: 400; font-size: 14px; margin-top: 4px; }
  .divider {
    position: absolute; left: 240px; top: 120px; width: 1px; height: 84px;
    background: linear-gradient(to bottom, transparent, var(--rule) 30%, var(--rule) 70%, transparent);
  }
  .contacts {
    position: absolute; left: 258px; top: 118px; list-style: none;
  }
  .contacts li {
    display: flex; align-items: center; gap: 9px;
    font-size: 15px; line-height: 1; height: 28px;
  }
  .contacts svg { width: 15px; height: 15px; flex: none; }
  .address-band {
    position: absolute; left: 0; right: 0; top: 222px; height: 36px;
    background: var(--ink); color: var(--paper);
    display: flex; align-items: center; gap: 8px; padding-left: 150px;
    font-size: 16px;
  }
  .address-band svg { width: 13px; height: 17px; }
</style>
</head>
<body>
<main class="stage">
  <section class="card card-back" aria-label="Card back">
    <div class="pattern-field" role="img" aria-label="Tone-on-tone repeated company wordmark pattern"></div>
    <p class="back-name">Veltrane</p>
  </section>

  <section class="card card-front" aria-label="Card front">
    <h1 class="company-name">Veltrane Group</h1>

    <div class="person">
      <p class="person-name">Rohesh Kamdar</p>
      <p class="person-title">CEO</p>
    </div>

    <div class="divider"></div>

    <ul class="contacts">
      <li>
        <svg viewBox="0 0 16 16" aria-hidden="true"><rect x="4" y="1" width="8" height="14" rx="1.5" fill="none" stroke="#000" stroke-width="1.4"/><line x1="7" y1="12.5" x2="9" y2="12.5" stroke="#000" stroke-width="1.2"/></svg>
        604.781.2249
      </li>
      <li>
        <svg viewBox="0 0 16 16" aria-hidden="true"><rect x="1" y="3" width="14" height="10" fill="#000"/><polyline points="1,3 8,9 15,3" fill="none" stroke="#fff" stroke-width="1.3"/></svg>
        roheshkamdar@veltrane.com
      </li>
      <li>
        <svg viewBox="0 0 16 16" aria-hidden="true"><circle cx="8" cy="8" r="6.5" fill="#000"/><ellipse cx="8" cy="8" rx="2.8" ry="6.5" fill="none" stroke="#fff" stroke-width="0.9"/><line x1="1.5" y1="8" x2="14.5" y2="8" stroke="#fff" stroke-width="0.9"/></svg>
        www.veltrane.com
      </li>
    </ul>

    <div class="address-band">
      <svg viewBox="0 0 12 16" aria-hidden="true"><path d="M6 0.8C3 0.8 0.8 3 0.8 5.8 0.8 9.5 6 15.2 6 15.2S11.2 9.5 11.2 5.8C11.2 3 9 0.8 6 0.8Z" fill="#fff"/><circle cx="6" cy="5.8" r="2" fill="#000"/></svg>
      4180 Lindqvist Ave, Tampa, FL 33482
    </div>
  </section>
</main>
</body>
</html>
```